Q&J RESTORATION

I want a brochure similiar to the example i've attached.
My company name is Northgate Home Repair. The website is: northgate-home.example.
The phone number is 919.555.0147.

I don't like the "yellow" being the main color of the example so I'm open to suggestions. I want something CLEAN & Simple, like our logo . This will be a bi fold brochure

```html
<!DOCTYPE html>
<html lang="en">
<head>
<meta charset="utf-8">
<title>Northgate Home Repair – Bi-fold Brochure</title>
<link rel="stylesheet" href="https://fonts.googleapis.com/css2?family=Montserrat:wght@400;500;600;700&display=swap">
<style>
  :root{
    --green:#049164;
    --green-bright:#06a070;
    --black:#0f0f0f;
    --charcoal:#1d1d1d;
    --frame-gray:#4a4a4a;
    --white:#ffffff;
    --paper:#e6e6e8;
    --muted:#d8d8d8;
  }
  *{margin:0;padding:0;box-sizing:border-box}
  html,body{width:1200px;height:2700px;overflow:hidden;background:var(--paper)}
  body{font-family:"Montserrat",Arial,sans-serif;position:relative}

  .spread{position:absolute;left:78px;width:995px;height:703px;transform:scale(1.0492);transform-origin:0 0;box-shadow:0 10px 28px rgba(0,0,0,.18)}
  .spread--outside{top:573px}
  .spread--inside{top:1433px}
  .panel{position:absolute;top:0;width:500px;height:703px;overflow:hidden}
  .panel--left{left:0}
  .panel--right{left:500px;width:495px}
  .panel svg.shapes{position:absolute;left:0;top:0;width:100%;height:100%}
  .abs{position:absolute}

  .brand-name{font-weight:500;color:var(--white);letter-spacing:.02em;white-space:nowrap}
  .brand-name--dark{color:var(--black)}
  .accent{color:var(--green-bright)}
  .web-url{font-weight:600;letter-spacing:.16em;color:var(--white);white-space:nowrap}

  /* back cover */
  .back-photo{position:absolute;inset:0;background:linear-gradient(160deg,#1b1b1b 0%,#121212 55%,#0d0d0d 100%)}
  .back-brand{left:42px;top:568px;font-size:15px}
  .back-tagline{left:42px;top:617px;font-size:17px;font-weight:600;line-height:23px;color:var(--white)}
  .contact-list{left:272px;top:586px;list-style:none}
  .contact-list li{display:flex;align-items:center;height:26.5px;font-size:11px;font-weight:500;color:var(--white);white-space:nowrap}
  .contact-list svg{width:18px;height:18px;margin-right:12px}

  /* front cover */
  .cover-brand{left:46px;top:50px;font-size:20px}
  .cover-title{right:50px;top:528px;text-align:right;font-size:34px;font-weight:700;line-height:42px;color:var(--white)}
  .cover-title .divider{display:inline-block;width:5px;height:32px;background:var(--green-bright);margin:0 10px;vertical-align:-4px}
  .cover-url{right:50px;top:638px;font-size:15px}

  /* inside left */
  .inside-title{left:41px;top:172px;font-size:36px;font-weight:700;line-height:38px;color:var(--white)}

  /* inside right */
  .steps-heading{left:53px;top:48px;font-size:21px;font-weight:600;color:var(--white)}
  .steps-sub{left:53px;top:81px;font-size:14px;font-weight:500;color:var(--white)}
  .step{left:53px;width:400px}
  .step__head{position:relative;height:26px}
  .step__num{position:absolute;left:0;top:-2px;width:28px;height:30px}
  .step__num span{position:absolute;inset:0;display:flex;align-items:center;justify-content:center;font-size:13px;font-weight:700;color:var(--black)}
  .step__label{position:absolute;left:30px;top:0;height:26px;width:206px;padding-left:10px;background:var(--green);clip-path:polygon(0 0,100% 0,93% 100%,0 100%);display:flex;align-items:center;font-size:12px;font-weight:600;color:var(--white);letter-spacing:.01em}
  .step__text{margin:10px 0 0 39px;width:335px;font-size:10.2px;line-height:12.6px;color:var(--muted)}
  .step--1{top:118px}
  .step--2{top:210px}
  .step--3{top:300px}
  .step--4{top:390px}
  .inside-brand{left:0;width:495px;top:522px;text-align:center;font-size:19px}
  .inside-url{left:0;width:495px;top:602px;text-align:center;font-size:17px}
</style>
</head>
<body>

<section class="spread spread--outside">
  <div class="panel panel--left back-cover">
    <div class="back-photo" role="img" aria-label="Dark, faint photo of a kitchen under renovation with a step ladder"></div>
    <div class="abs brand-name back-brand">Northgate Home Repair</div>
    <p class="abs back-tagline"><span class="accent">INSURANCE CLAIM?</span><br>WE'RE ON YOUR TEAM.</p>
    <ul class="abs contact-list">
      <li>
        <svg viewBox="0 0 20 20"><polygon points="10,0 18.7,5 18.7,15 10,20 1.3,15 1.3,5" fill="var(--green)"/><path d="M6.5 5.5l2 0 1 2.5-1.3 1a6 6 0 0 0 3 3l1-1.3 2.5 1v2c-5 .3-8.5-3.2-8.2-8.2z" fill="#fff"/></svg>
        919.555.0147
      </li>
      <li>
        <svg viewBox="0 0 20 20"><polygon points="10,0 18.7,5 18.7,15 10,20 1.3,15 1.3,5" fill="var(--green)"/><rect x="5.5" y="6.5" width="9" height="7" fill="none" stroke="#fff" stroke-width="1.2"/><path d="M5.5 6.5l4.5 4 4.5-4" fill="none" stroke="#fff" stroke-width="1.2"/></svg>
        info@northgate-home.example
      </li>
      <li>
        <svg viewBox="0 0 20 20"><polygon points="10,0 18.7,5 18.7,15 10,20 1.3,15 1.3,5" fill="var(--green)"/><circle cx="10" cy="10" r="4.5" fill="none" stroke="#fff" stroke-width="1.1"/><path d="M5.5 10h9M10 5.5c-2.4 3-2.4 6 0 9M10 5.5c2.4 3 2.4 6 0 9" fill="none" stroke="#fff" stroke-width="1"/></svg>
        www.northgate-home.example
      </li>
    </ul>
  </div>

  <div class="panel panel--right front-cover">
    <svg class="shapes" viewBox="0 0 495 703" preserveAspectRatio="none">
      <defs>
        <linearGradient id="coverBandFade" x1="0" y1="0" x2="1" y2="0">
          <stop offset="0" stop-color="var(--green)" stop-opacity=".95"/>
          <stop offset="1" stop-color="var(--green)" stop-opacity=".55"/>
        </linearGradient>
        <linearGradient id="siteTone" x1="0" y1="0" x2="0" y2="1">
          <stop offset="0" stop-color="#262626"/>
          <stop offset="1" stop-color="#141414"/>
        </linearGradient>
        <linearGradient id="cityTone" x1="0" y1="0" x2="0" y2="1">
          <stop offset="0" stop-color="#ececec"/>
          <stop offset=".45" stop-color="#9a9a9a"/>
          <stop offset="1" stop-color="#3c3c3c"/>
        </linearGradient>
      </defs>
      <rect width="495" height="703" fill="var(--white)"/>
      <polygon points="0,440 495,165 495,703 0,703" fill="url(#siteTone)" role="img" aria-label="Dark photo of a construction site"/>
      <polygon points="0,445 250,306 180,392 0,492" fill="url(#coverBandFade)"/>
      <polygon points="433,0 495,0 495,160 447,186 283,86" fill="var(--green)"/>
      <polygon points="274,93 445,191.5 445,388.5 274,487 103,388.5 103,191.5" fill="var(--frame-gray)"/>
      <polygon points="274,110 430,200 430,380 274,470 118,380 118,200" fill="var(--white)"/>
      <polygon points="274,125 417,207.5 417,372.5 274,455 131,372.5 131,207.5" fill="url(#cityTone)" role="img" aria-label="Black and white photo of a city skyline with tall towers"/>
      <polygon points="380,392 433,422 433,484 380,514 327,484 327,422" fill="none" stroke="#6a6a6a" stroke-width="1.5"/>
      <polygon points="403,403 448,429 448,481 403,507 358,481 358,429" fill="var(--green-bright)"/>
    </svg>
    <div class="abs brand-name brand-name--dark cover-brand">Northgate Home Repair</div>
    <h1 class="abs cover-title">BUILD<span class="divider"></span>RENOVATE<br>RESTORE</h1>
    <div class="abs web-url cover-url">www.<span class="accent">northgate-home</span>.example</div>
  </div>
</section>

<section class="spread spread--inside">
  <div class="panel panel--left inside-left">
    <svg class="shapes" viewBox="0 0 500 703" preserveAspectRatio="none">
      <defs>
        <linearGradient id="towerGreen" x1="0" y1="0" x2="0" y2="1">
          <stop offset="0" stop-color="var(--green)"/>
          <stop offset=".6" stop-color="#0c5a40"/>
          <stop offset="1" stop-color="#0f2a20"/>
        </linearGradient>
        <linearGradient id="workerTone" x1="0" y1="0" x2="1" y2="1">
          <stop offset="0" stop-color="#c9c4bf"/>
          <stop offset="1" stop-color="#6f6a66"/>
        </linearGradient>
        <linearGradient id="coupleTone" x1="0" y1="0" x2="1" y2="1">
          <stop offset="0" stop-color="#9aa8b4"/>
          <stop offset="1" stop-color="#5d6b7a"/>
        </linearGradient>
      </defs>
      <rect width="500" height="703" fill="var(--black)"/>
      <polygon points="178,325 500,135 500,703 220,703" fill="url(#towerGreen)" role="img" aria-label="Green-tinted photo of high-rise towers under construction"/>
      <polygon points="345,-125 488,-42.5 488,122.5 345,205 202,122.5 202,-42.5" fill="var(--frame-gray)"/>
      <polygon points="345,-110 475,-35 475,115 345,190 215,115 215,-35" fill="var(--white)"/>
      <polygon points="345,-98 464.5,-29 464.5,109 345,178 225.5,109 225.5,-29" fill="url(#workerTone)" role="img" aria-label="Photo of a tradesman measuring a countertop in a renovated room"/>
      <polygon points="190,318 362,417 362,617 190,716 18,617 18,417" fill="#333"/>
      <polygon points="173,330 342,427.5 342,622.5 173,720 4,622.5 4,427.5" fill="var(--frame-gray)"/>
      <polygon points="173,345 329,435 329,615 173,705 17,615 17,435" fill="var(--white)"/>
      <polygon points="173,359 316.8,442 316.8,608 173,691 29.2,608 29.2,442" fill="url(#coupleTone)" role="img" aria-label="Photo of a happy couple standing in front of their restored home"/>
    </svg>
    <h2 class="abs inside-title">BUILD<br>RENOVATE<br>RESTORE</h2>
  </div>

  <div class="panel panel--right inside-right">
    <svg class="shapes" viewBox="0 0 495 703" preserveAspectRatio="none">
      <defs>
        <linearGradient id="skyscraperFade" x1="1" y1="0" x2="0" y2="1">
          <stop offset="0" stop-color="#3a3a3a"/>
          <stop offset=".5" stop-color="#242424"/>
          <stop offset="1" stop-color="#1a1a1a"/>
        </linearGradient>
      </defs>
      <rect width="495" height="703" fill="url(#skyscraperFade)" role="img" aria-label="Dark, faint photo of skyscrapers seen from below"/>
    </svg>
    <h3 class="abs steps-heading">WATER OR <span class="accent">MOLD DAMAGE?</span></h3>
    <p class="abs steps-sub">What happens after the cleanup?</p>

    <div class="abs step step--1">
      <div class="step__head">
        <div class="step__num"><svg viewBox="0 0 28 30"><polygon points="14,1 27,8.5 27,21.5 14,29 1,21.5 1,8.5" fill="var(--white)"/></svg><span>1</span></div>
        <div class="step__label">ADJUSTER'S INSPECTION</div>
      </div>
      <p class="step__text">Feel Confident. Be sure you received a fair and accurate assessment &amp; repair of all damages with our team's use of industry leading Estimating Systems and On-Site Review.</p>
    </div>
    <div class="abs step step--2">
      <div class="step__head">
        <div class="step__num"><svg viewBox="0 0 28 30"><polygon points="14,1 27,8.5 27,21.5 14,29 1,21.5 1,8.5" fill="var(--white)"/></svg><span>2</span></div>
        <div class="step__label">TIMELY SETTLEMENT</div>
      </div>
      <p class="step__text">Don't wait. Minimize the hassle of long processing times from Estimate to Settlement when you team up with an Insurance Repair Specialist.</p>
    </div>
    <div class="abs step step--3">
      <div class="step__head">
        <div class="step__num"><svg viewBox="0 0 28 30"><polygon points="14,1 27,8.5 27,21.5 14,29 1,21.5 1,8.5" fill="var(--white)"/></svg><span>3</span></div>
        <div class="step__label">UNDER ONE ROOF</div>
      </div>
      <p class="step__text">Don't Worry. You won't need to arrange meetings with multiple contractors; we'll take care of everything from demo to final cleanup.</p>
    </div>
    <div class="abs step step--4">
      <div class="step__head">
        <div class="step__num"><svg viewBox="0 0 28 30"><polygon points="14,1 27,8.5 27,21.5 14,29 1,21.5 1,8.5" fill="var(--white)"/></svg><span>4</span></div>
        <div class="step__label">SUPERIOR CRAFTSMANSHIP</div>
      </div>
      <p class="step__text">Don't settle for satisfactory. Our team is committed to the highest standards of excellence every step of the way. Trust us when we say that we'll make you smile.</p>
    </div>

    <div class="abs brand-name inside-brand">Northgate Home Repair</div>
    <div class="abs web-url inside-url">www.<span class="accent">northgate-home</span>.example</div>
  </div>
</section>

</body>
</html>
```